Velmoria-Quillmesh Partial Redesign - Web App

Are you able to apply your creativity to an existing layout? I’m convinced that even just a few touches can make a big difference to add personality and professionalism to a website design, and I’m looking for someone able to use existing ideas and bring them to the next level while keeping inside some given constraints.
The actual job is to improve an existing design concept and to apply it creatively to a landing page, a simple home page, and an older web app (single page website).
To help you start with a clear picture of the current situation and of my requirements, I created a detailed brief with screenshots, live examples, and complete instructions. You can find it attached to this job.
My tastes are inclined towards clean and simple designs. For this project I'm not looking for dazzling novelty, but for very solid craftsmanship. Are the right man - or woman - for the job?
Updates
I wanted to thank everybody who participated in this project. I made a choice, but also other designs were interesting. Hope to work with you another time.
Target Market(s)
Our main target is social media marketers and startuppers
Look and feel
Each slider illustrates characteristics of the customer's brand and the style your logo design should communicate.

```html
<!DOCTYPE html>
<html lang="en">
<head>
<meta charset="utf-8">
<title>Quillmesh – Hashtag Explorer</title>
<link href="https://fonts.googleapis.com/css2?family=Arimo:wght@400;700&display=swap" rel="stylesheet">
<style>
:root{
  --page-bg:#f6f6f6;
  --panel:#ffffff;
  --text:#111111;
  --link:#2a8ad0;
  --muted:#b0b0b0;
  --node-core:#3d93cf;
  --node-blue:#abd1e8;
  --node-teal:#c9e1e1;
  --node-gray:#9a9a9a;
  --node-faint:#eeeeee;
  --edge-blue:#9cc8e6;
  --edge-gray:#e6e6e6;
  --tab-off:#dadada;
  --footer-top:#343434;
  --footer-bottom:#202020;
  --footer-text:#ffffff;
}
*{box-sizing:border-box;margin:0;padding:0}
html,body{width:1200px;height:959px;overflow:hidden;background:var(--page-bg)}
body{font-family:"Arimo",Arial,sans-serif;color:var(--text)}
.page{position:relative;width:1020px;height:815px;transform:scale(1.17647);transform-origin:0 0;background:var(--page-bg)}
.graph-panel{position:absolute;left:40px;top:0;width:620px;height:450px;background:var(--panel);border-radius:0 0 6px 6px;overflow:hidden}
.graph-panel svg{display:block}
.node-label{font-family:"Arimo",Arial,sans-serif;font-size:13px;fill:var(--text);text-anchor:middle;dominant-baseline:middle}
.node-label--strong{font-weight:700}
.mode-tabs{position:absolute;left:440px;top:450px;height:32px;display:flex}
.mode-tab{font-size:12px;padding:7px 14px 0;height:32px}
.mode-tab--simple{background:var(--tab-off);clip-path:polygon(0 0,100% 0,100% 100%,10px 100%)}
.mode-tab--advanced{background:var(--panel);clip-path:polygon(0 0,100% 0,calc(100% - 10px) 100%,10px 100%);padding:7px 20px 0 10px}
.search-hint{position:absolute;left:49px;top:507px;font-size:13px}
.tweet-feed{position:absolute;left:680px;top:12px;width:305px;list-style:none}
.tweet{font-size:12px;line-height:18px;margin-bottom:18px;overflow:hidden}
.tweet__avatar{float:left;width:24px;height:24px;margin:2px 12px 0 1px}
.tweet__user,.tweet a{color:var(--link);text-decoration:none}
.tweet__time{color:var(--muted);font-style:italic}
.site-footer{position:absolute;left:0;top:696px;width:1020px;height:119px;background:linear-gradient(var(--footer-top),var(--footer-bottom));color:var(--footer-text);font-size:12px}
.brand{position:absolute;left:40px;top:16px;width:143px;height:40px;border-bottom:1px solid #444;display:flex;align-items:flex-start;gap:8px}
.brand__mark{width:16px;height:16px;background:var(--footer-text);margin-top:7px}
.brand__name{font-size:16px;font-weight:700;line-height:30px}
.address{position:absolute;left:40px;top:68px;line-height:20px;font-style:normal}
.copyright{position:absolute;left:415px;top:78px}
.legal-links{position:absolute;right:40px;top:78px;display:flex;gap:14px}
.legal-links a{color:var(--footer-text);text-decoration:none}
</style>
</head>
<body>
<div class="page">
  <section class="graph-panel">
    <svg width="620" height="450" viewBox="40 0 620 450" aria-label="Related hashtag graph">
      <g stroke="var(--edge-gray)" stroke-width="4">
        <line x1="300" y1="99" x2="100" y2="14"/>
        <line x1="300" y1="99" x2="228" y2="5"/>
        <line x1="300" y1="99" x2="300" y2="0"/>
        <line x1="300" y1="99" x2="360" y2="0"/>
        <line x1="300" y1="99" x2="428" y2="44"/>
        <line x1="300" y1="99" x2="472" y2="121"/>
        <line x1="300" y1="99" x2="158" y2="121"/>
      </g>
      <g stroke="var(--edge-blue)" stroke-width="5">
        <line x1="454" y1="272" x2="428" y2="44"/>
        <line x1="454" y1="272" x2="472" y2="121"/>
        <line x1="454" y1="272" x2="578" y2="155"/>
        <line x1="454" y1="272" x2="158" y2="121"/>
        <line x1="454" y1="272" x2="234" y2="217"/>
        <line x1="454" y1="272" x2="122" y2="332"/>
        <line x1="454" y1="272" x2="269" y2="357"/>
        <line x1="454" y1="272" x2="368" y2="393"/>
        <line x1="454" y1="272" x2="182" y2="430"/>
      </g>
      <line x1="300" y1="99" x2="454" y2="272" stroke="var(--node-gray)" stroke-width="10"/>
      <circle cx="100" cy="14" r="33" fill="var(--node-faint)"/>
      <circle cx="228" cy="5" r="32" fill="var(--node-faint)"/>
      <circle cx="360" cy="-2" r="24" fill="var(--node-faint)"/>
      <circle cx="300" cy="99" r="56" fill="var(--node-gray)"/>
      <circle cx="428" cy="44" r="52" fill="var(--node-blue)"/>
      <circle cx="472" cy="121" r="33" fill="var(--node-teal)"/>
      <circle cx="578" cy="155" r="52" fill="var(--node-blue)"/>
      <circle cx="158" cy="121" r="33" fill="var(--node-teal)"/>
      <circle cx="234" cy="217" r="52" fill="var(--node-blue)"/>
      <circle cx="122" cy="332" r="52" fill="var(--node-blue)"/>
      <circle cx="269" cy="357" r="52" fill="var(--node-blue)"/>
      <circle cx="368" cy="393" r="52" fill="var(--node-blue)"/>
      <circle cx="182" cy="432" r="52" fill="var(--node-blue)"/>
      <circle cx="454" cy="272" r="88" fill="var(--node-core)"/>
      <text class="node-label" x="100" y="15">people</text>
      <text class="node-label" x="228" y="6">in</text>
      <text class="node-label node-label--strong" x="300" y="102">hashtags</text>
      <text class="node-label" x="428" y="45">in</text>
      <text class="node-label" x="470" y="124">like</text>
      <text class="node-label" x="578" y="156">use</text>
      <text class="node-label" x="159" y="122">tweet</text>
      <text class="node-label" x="234" y="218">you</text>
      <text class="node-label" x="122" y="333">in</text>
      <text class="node-label" x="270" y="360">people</text>
      <text class="node-label" x="367" y="394">tweet</text>
      <text class="node-label" x="182" y="437">to</text>
      <text class="node-label node-label--strong" x="451" y="278">the</text>
    </svg>
  </section>

  <nav class="mode-tabs">
    <span class="mode-tab mode-tab--simple">Simple mode</span>
    <span class="mode-tab mode-tab--advanced">Advanced mode</span>
  </nav>

  <p class="search-hint">Find all trending related hashtags for #tag with</p>

  <ul class="tweet-feed">
    <li class="tweet"><span class="tweet__avatar" role="img" aria-label="User avatar" style="background:linear-gradient(#6a80b8,#e0b060)"></span><a class="tweet__user">pellimo22:</a> I wonder why people have to put <a>#hashtags</a> on <a>#SN</a>. <span class="tweet__time">2 minutes ago</span></li>
    <li class="tweet"><span class="tweet__avatar" role="img" aria-label="User avatar" style="background:#a89098"></span><a class="tweet__user">Rina_Maren07:</a> My favorite part of Chirper <a>#hashtags</a> <span class="tweet__time">5 minutes ago</span></li>
    <li class="tweet"><span class="tweet__avatar" role="img" aria-label="User avatar" style="background:#9a8088"></span><a class="tweet__user">tomvardaxen:</a> <a>@lunafelk</a> 4-12 black FEIDAY <a>#blackfeiday</a> <a>#BLACKFRIDAYMADNESS</a> <a>#baristaproblems</a> <a>#hashtags</a> <span class="tweet__time">5 minutes ago</span></li>
    <li class="tweet"><span class="tweet__avatar" role="img" aria-label="User avatar" style="background:#f3a860"></span><a class="tweet__user">davosperrin:</a> <a>#Count</a> <a>#Your</a> <a>#Hashtags</a> -- <a>#AndMore</a>: <a>http://ex.io/qaPLmT</a> ~ via <a>@NorthLUMAR</a> <span class="tweet__time">6 minutes ago</span></li>
    <li class="tweet"><span class="tweet__avatar" role="img" aria-label="User avatar" style="background:linear-gradient(#c89050,#403028)"></span><a class="tweet__user">OddlyFinn:</a> <a>@K9_X4T</a> part of me doesnt understand.... but the other part of me under-stands too much <a>#deepthoughts</a> <span class="tweet__time">8 minutes ago</span></li>
    <li class="tweet"><span class="tweet__avatar" role="img" aria-label="User avatar" style="background:#3d8ee8"></span><a class="tweet__user">Zeb_Lo:</a> <a>@mikotarnel3</a> did you have it teed up ?:/ sorry I didn't click on... <a>#failure</a> <a>#killmyself</a> <a>#death</a> <a>#sadness</a> <a>#hashtags</a> <span class="tweet__time">8 minutes ago</span></li>
    <li class="tweet"><span class="tweet__avatar" role="img" aria-label="User avatar" style="background:radial-gradient(#fff4d0,#8090c0)"></span><a class="tweet__user">olsenvira:</a> to <a>#getmorefollowers</a> instantly ,follow <a>#hashtags</a> <a>#TeamFollowBack</a>, <a>#InstantFollowBack</a>, <a>#AutoFollowBack</a>, <a>#100ADAY</a>, <a>#500ADAY</a>, <a>#1000ADAY</a> <span class="tweet__time">12 minutes ago</span></li>
    <li class="tweet"><span class="tweet__avatar" role="img" aria-label="User avatar" style="background:#6a4a30"></span><a class="tweet__user">ruu_pel_ox:</a> THE END OF HUMANITY - UTOPIA 666 <a>http://ex.io/hr4pWmzd</a> <a>#hashtags</a> <a>#like</a> <a>UK</a> <a>#summer2012</a> <a>#modpen2012</a> <a>#Summergames</a> <a>#Brazil</a> <a>#alchemix</a> <a>#i</a> <a>#hate</a> <a>#when</a> <span class="tweet__time">13 minutes ago</span></li>
    <li class="tweet"><span class="tweet__avatar" role="img" aria-label="User avatar" style="background:linear-gradient(#d0d8e8,#505870)"></span><a class="tweet__user">SolRepostBot:</a> RT <a>@ruu_pel_ox</a>: THE END OF HUMANITY - UTOPIA 666 <a>http://ex.io/hr4pWmzd</a> <a>#people</a> <a>#use</a> <a>#hashtags</a> <a>#like</a> <a>#this</a> <a>#summer2012</a> <a>#modpen2012</a> <a>#Summergames</a> <a>#Brazil</a> <a>brasil</a> <a>UK</a> <span class="tweet__time">15 minutes ago</span></li>
  </ul>

  <footer class="site-footer">
    <div class="brand"><span class="brand__mark"></span><span class="brand__name">Velmoria</span></div>
    <address class="address">14 Larch Lane<br>K7 4RT Dunmere, UK</address>
    <p class="copyright">Copyright © 2012 Velmoria Ltd.</p>
    <nav class="legal-links"><a>Private Policy</a><a>Term Of Services</a></nav>
  </footer>
</div>
</body>
</html>
```